Stationery Design Project

We need a stationery design for our Norwegian trucking company. We have existed for about 15 years and our 12 drivers uses relatively new vehicles to transport goods around in northern Norway. Long distance routes with fresh fish og food transport is our main operations.

We have already made alogo that's printed on our trucks. The logo and a picture of our trucks is attached. I think the logo i crappy, but since its already in use, changing it is not an option in this round. Still using a better colour scheme in the overall stationery and more interesting fonts is possible (altso in the logo).

Company details:
Name: Kjelvraket AS
Organisation nr 873 615 309
Post adress: 8642 Raudvik

I like minimalism and simplicity. I am avalibly for questions in normal GMT working hours either here or on mail: ivar@fjordlast.no

Reason: Hi. Im extending the deadline because I needed some time to find a vector file of our logo. Sorry for the inconvenience

Hi, and thanks for all your interest in the project. Some updates:

-          I have decided to commit to using one of the designs. Some designer will get the payment.

-          I have extended the deadline with 24 hours since I needed some time to find our firms vector logo (a slow Swedish man was holding me up)

-          We will not choose a design before the deadline. No need to rush.

-          We have received a lot of great design and think there is a need to specified the product we want to make:

o   Business Card for all our employers. I just need the design and will duplicate with the correct numbers and name myself. The information on should be: Logo, employer’s name, Phone number, email, website, Postal number and address. Use this as a template: logo, Leif Brattvoll, 47382066, Leif@fjordlast.no,, fjordlast.no, 8642 Raudvik. The order and placement of the information is your creative decision.

o   Stickers to put on the goods we travel. On the sticker the should be the following information: Logo, phone number, Tekst and link: Fraktæ av Kjelvraket. Ke du syns? Fjordlast.no/tilbakemelding (this means: Handled by Kjelvraket. What do you think Fjordlast.no/feedback -à the link will be a feedback form). The placement the information and size is your creative decision with some stings: we have been thinking of using Drukko for printing and see that a size about 6x6 cm, 8x5 or something like that. (with 3000 copies our budget is 200 punds). Any suggestions of other suppliers are welcome. Drukko price calculator http://www.drukkolabelhouse.co.uk/digital-litho-printing/printing-labels-tags/stickers/

o   Letterhead with logo, address, phone number and organizational number.

o   Envelopes with logo,address, phone number and organizational number.

Have a nice day.

 

 

• Using the blue colour in the logo and using a similar graphic approch.

```html
<!DOCTYPE html>
<html lang="no">
<head>
<meta charset="utf-8">
<title>Kjelvraket AS – visittkort</title>
<link rel="stylesheet" href="https://fonts.googleapis.com/css2?family=Source+Sans+3:wght@400;600;700&display=swap">
<style>
  :root {
    --backdrop: #b9b9b9;
    --paper: #ffffff;
    --navy: #0b4fa3;
    --azure: #0a74bd;
    --ink: #1d1d1d;
    --rule: #c9c9c9;
    --font: "Source Sans 3", Arial, sans-serif;
  }
  * { box-sizing: border-box; margin: 0; padding: 0; }
  html, body { width: 1200px; height: 711px; overflow: hidden; }
  body { background: var(--backdrop); font-family: var(--font); position: relative; }

  .card {
    position: absolute;
    width: 514px; height: 294px;
    box-shadow: 0 1px 3px rgba(0,0,0,.25);
    overflow: hidden;
  }
  .card--front { left: 66px; top: 45px; background: var(--paper); }
  .card--navy  { left: 620px; top: 45px; background: var(--navy); }
  .card--white { left: 66px; top: 370px; background: var(--paper); }
  .card--azure { left: 620px; top: 370px; background: var(--azure); }

  .wordmark {
    position: absolute; left: 0; right: 0;
    display: flex; align-items: center; justify-content: center; gap: 14px;
    font-weight: 700; font-size: 58px; letter-spacing: .5px;
    color: var(--navy);
  }
  .wordmark__dot { width: 22px; height: 22px; border-radius: 50%; background: currentColor; }
  .card--navy .wordmark, .card--azure .wordmark { color: var(--paper); }
  .card--front .wordmark { top: 62px; }
  .card--navy .wordmark, .card--white .wordmark, .card--azure .wordmark { top: 100px; }

  .website {
    position: absolute; left: 0; right: 0; bottom: 26px;
    text-align: center; font-size: 18px; letter-spacing: 4px; color: var(--ink);
  }
  .card--navy .website, .card--azure .website { color: var(--paper); }

  .person {
    position: absolute; right: 270px; top: 194px; text-align: right; color: var(--navy);
  }
  .person__name { font-weight: 700; font-size: 19px; line-height: 22px; }
  .person__org { font-size: 15px; line-height: 20px; }
  .person__org span { color: var(--ink); }

  .divider { position: absolute; left: 266px; top: 183px; width: 1px; height: 72px; background: var(--rule); }

  .contact { position: absolute; left: 279px; top: 188px; list-style: none; font-size: 15.5px; color: var(--ink); }
  .contact li { display: flex; align-items: center; gap: 6px; line-height: 21px; }
  .contact svg { width: 10px; height: 10px; fill: var(--navy); }

  .band { position: absolute; left: 0; right: 0; bottom: 0; height: 23px; }
  .band__site {
    position: absolute; right: 54px; bottom: 2px;
    font-size: 15px; letter-spacing: 3px; color: var(--paper);
  }
</style>
</head>
<body>

<section class="card card--front" aria-label="Visittkort forside">
  <div class="wordmark"><span class="wordmark__dot"></span>Kjelvraket</div>

  <div class="person">
    <p class="person__name">Leif Brattvoll</p>
    <p class="person__org">Org nr <span>873 615 309</span></p>
  </div>
  <div class="divider"></div>
  <ul class="contact">
    <li><svg viewBox="0 0 10 10"><path d="M1 9V4l4-3 4 3v5H6V6H4v3z"/></svg>8642 Raudvik</li>
    <li><svg viewBox="0 0 10 10"><path d="M2 1l2 .3.6 2-1 1a6 6 0 0 0 2.1 2.1l1-1 2 .6L9 8 7.8 9C4.5 9 1 5.5 1 2.2z"/></svg>47382066</li>
    <li><svg viewBox="0 0 10 10"><path d="M1 3h8v6H1zM1 3l4 3 4-3"/></svg>Leif@fjordlast.no</li>
  </ul>

  <svg class="band" viewBox="0 0 514 23" preserveAspectRatio="none" aria-hidden="true">
    <polygon points="0,0 258,0 242,23 0,23" fill="var(--azure)"/>
    <polygon points="266,0 514,0 514,23 250,23" fill="var(--navy)"/>
  </svg>
  <p class="band__site">www.fjordlast.no</p>
</section>

<section class="card card--navy" aria-label="Visittkort bakside, mørk blå">
  <div class="wordmark"><span class="wordmark__dot"></span>Kjelvraket</div>
  <p class="website">www.fjordlast.no</p>
</section>

<section class="card card--white" aria-label="Visittkort bakside, hvit">
  <div class="wordmark"><span class="wordmark__dot"></span>Kjelvraket</div>
  <p class="website">www.fjordlast.no</p>
</section>

<section class="card card--azure" aria-label="Visittkort bakside, lys blå">
  <div class="wordmark"><span class="wordmark__dot"></span>Kjelvraket</div>
  <p class="website">www.fjordlast.no</p>
</section>

</body>
</html>
```